Fitness Equipment & Service

I want to make the card eye catching and fun. We are called Corvane Motion Limited and we are based in Wales. We sell, install and service all types of fitness equipment from Skipping ropes, right through the Dumbbells, Kettle bells and Barbells through to state of the art Treadmills, Running Machines and Strength Equipment. We also design and install changing room furniture and lockers.

TYPOGRAPHY
We would like to use Futrura. Futura has an appearance of efficiency and forwardness. The typeface is derived
from simple geometric forms (near-perfect circles, triangles and squares) and is based on strokes of
near-even weight, which are low in contrast. This is most visible in the almost perfectly round stroke of
the o, which is nonetheless slightly ovoid.
The lowercase has tall ascenders, which rise above the cap line. The uppercase
characters present proportions similar to those of classical Roman capitals.

TYPOGRAPHIC CONSIDERATIONS
No Strike though
No Horizontal Scaling
No Drop Shadows
No Effects
Never use less than 120% Leading

OUR CORPORATE COLOURS
BRAND GUIDELINES
We were thinking that our primary colour palette consists of the Acid Green (Pantone 382) and Process Black.

We work closely with tquarly Ltd and would like to include their name on the card somewhere. I have attached images of the other brands that we work with as an idea or the small icons I have included that illustrate what we do?. I have very kindly been given permission to use any of the images off the files that I have included below, so I hope these help. I will include these below. I would be open to suggestions if it made the card more striking Can you do it?
Updates

Hi All, Just wanted to add a few thoughts but you are the guys with the creative visions (thats why are here) We are based in Wales, UK and we would be open to lots of different ideas on a theme but must be eye catching, Bold and FUN. If you can or think that the Welsh or any dragon could be put in there then go for it (its not a must have) We have also added some ideas for colour but again its over to you!! GO FOR IT ! Thanks and look forward to your visions! Owen

Hi All, Just thought I would sen through the contact details that need to be on the card. (if you want to play around with icons instead of the wording twitter, Facebook, go for it): Corvane Motion Limited Owen Pritchard Managing Director Mob: +44 (0)7582 913 406 e-mail: sales@corvanemotion.co.uk Web: Corvanemotion.co.uk twitter: @motionLetterbin Facebook: Corvane Motion Limited

```html
<!DOCTYPE html>
<html lang="en">
<head>
<meta charset="utf-8">
<title>Corvane Motion Limited – Business Card</title>
<link href="https://fonts.googleapis.com/css2?family=Jost:wght@400;500;600&display=swap" rel="stylesheet">
<style>
  :root {
    --backdrop: #8c8c8c;
    --card: #ffffff;
    --navy-deep: #142a6e;
    --navy: #1d3a8f;
    --navy-light: #2b4fae;
    --gold: #b8913a;
    --gold-light: #d9b65e;
    --ink: #141a3c;
    --text-grey: #4a4a4a;
    --white: #ffffff;
    --mark: #1f3c90;
  }
  * { box-sizing: border-box; margin: 0; padding: 0; }
  html, body { width: 1105px; height: 1200px; overflow: hidden; }
  body {
    background: var(--backdrop);
    font-family: "Jost", "Futura", sans-serif;
    position: relative;
  }
  .card {
    position: absolute;
    left: 182px;
    width: 746px;
    height: 426px;
    background: var(--card);
    overflow: hidden;
  }
  .card--front { top: 119px; }
  .card--back { top: 636px; }

  /* Front */
  .info-band {
    position: absolute;
    left: 0; top: 69px;
    width: 100%; height: 249px;
    background: linear-gradient(90deg, var(--gold) 0%, var(--gold-light) 14%, var(--gold) 24%, var(--navy-deep) 27%, var(--navy) 55%, var(--navy-light) 80%, var(--navy-deep) 100%);
  }
  .brand-seal {
    position: absolute;
    left: 96px; top: 74px;
    width: 244px; height: 244px;
  }
  .contact {
    position: absolute;
    left: 391px; top: 80px;
    color: var(--white);
    line-height: 1.25;
  }
  .contact__name { font-size: 31px; font-weight: 500; }
  .contact__role { font-size: 22px; font-weight: 400; opacity: .88; margin-bottom: 10px; }
  .contact__address { font-size: 20px; margin-bottom: 10px; }
  .contact__line {
    display: flex; align-items: center; gap: 9px;
    font-size: 20px; height: 28px;
  }
  .contact__line svg { width: 18px; height: 18px; flex: none; }
  .social {
    position: absolute;
    left: 0; right: 0; top: 340px;
    text-align: center;
    font-size: 21px;
    line-height: 1.35;
    color: var(--text-grey);
  }
  .social__label { color: var(--ink); font-weight: 600; }

  /* Back */
  .back-mark {
    position: absolute;
    left: 276px; top: 69px;
    width: 194px; height: 194px;
    border-radius: 50%;
    background: var(--mark);
  }
  .back-name {
    position: absolute;
    left: 0; right: 0; top: 300px;
    text-align: center;
    font-size: 34px;
    font-weight: 600;
    line-height: 1.2;
    color: var(--ink);
  }
</style>
</head>
<body>

<section class="card card--front">
  <div class="info-band"></div>
  <svg class="brand-seal" viewBox="0 0 244 244">
    <circle cx="122" cy="122" r="120" fill="var(--mark)"/>
    <text x="122" y="116" text-anchor="middle" font-family="Jost, sans-serif" font-size="24" font-weight="500" fill="#ffffff">Corvane Motion</text>
    <text x="122" y="146" text-anchor="middle" font-family="Jost, sans-serif" font-size="24" font-weight="500" fill="#ffffff">Limited</text>
  </svg>

  <div class="contact">
    <p class="contact__name">Owen Pritchard</p>
    <p class="contact__role">Managing Director</p>
    <p class="contact__address">4218 Harrowfield Lane<br>Brynmawr, Gwent 40261</p>
    <p class="contact__line">
      <svg viewBox="0 0 18 18"><rect x="4" y="1" width="10" height="16" rx="2" fill="none" stroke="#fff" stroke-width="1.8"/><line x1="7.5" y1="14" x2="10.5" y2="14" stroke="#fff" stroke-width="1.5"/></svg>
      +44 (0)7582 913 406
    </p>
    <p class="contact__line">
      <svg viewBox="0 0 18 18"><rect x="1" y="4" width="16" height="11" fill="#fff"/><path d="M1 4 L9 10 L17 4" fill="none" stroke="var(--navy)" stroke-width="1.4"/></svg>
      sales@corvanemotion.co.uk
    </p>
    <p class="contact__line">
      <svg viewBox="0 0 18 18"><circle cx="9" cy="9" r="8" fill="#fff"/><ellipse cx="9" cy="9" rx="3.5" ry="8" fill="none" stroke="var(--navy)" stroke-width="1.2"/><line x1="1" y1="9" x2="17" y2="9" stroke="var(--navy)" stroke-width="1.2"/></svg>
      www.Corvanemotion.co.uk
    </p>
  </div>

  <div class="social">
    <p><span class="social__label">Twitter:</span> @motionLetterbin</p>
    <p><span class="social__label">Facebook:</span> Corvane Motion Limited</p>
  </div>
</section>

<section class="card card--back">
  <div class="back-mark"></div>
  <p class="back-name">Corvane Motion Limited</p>
</section>

</body>
</html>
```